Construction Company

Design a clutter free business card, it can be double-sided utilizing the logo for VKM Ltd simple with all relevant contact information.

Please also a letterhead design to function for the purposes of invoicing, all mail requirements, with header to be distinctive while the footer ties page together and incorporates all necessary information.

For now, please use generic / dummy text and when a winner is selected, I will disclose the contact information.

Hi Designers! Please read the updated brief which includes the design of a business card and letterhead. Thank you!

```html
<!DOCTYPE html>
<html lang="en">
<head>
<meta charset="UTF-8">
<title>VKM Ltd Business Card</title>
<link href="https://fonts.googleapis.com/css2?family=Montserrat:wght@500;600;700&display=swap" rel="stylesheet">
<style>
  :root {
    --stage: #1e1e1f;
    --royal: #0f2f98;
    --royal-light: #1d45b5;
    --gold: #c39a2a;
    --white: #ffffff;
  }
  * { margin: 0; padding: 0; box-sizing: border-box; }
  html, body { width: 1200px; height: 930px; overflow: hidden; }
  body {
    background: var(--stage);
    font-family: 'Montserrat', Arial, sans-serif;
    position: relative;
  }
  .card {
    position: absolute;
    width: 560px;
    height: 320px;
    border-radius: 22px;
    overflow: hidden;
    background: linear-gradient(135deg, var(--royal) 0%, var(--royal-light) 50%, var(--royal) 100%);
  }
  .card--front { left: 80px; top: 110px; }
  .card--back { left: 560px; top: 500px; }

  .wordmark {
    font-weight: 700;
    letter-spacing: 2px;
    white-space: nowrap;
  }
  .card--front .wordmark {
    position: absolute;
    left: 0; right: 0; top: 0; bottom: 0;
    display: flex; align-items: center; justify-content: center;
    color: var(--white);
    font-size: 64px;
  }

  .back-art { position: absolute; inset: 0; }
  .card--back .wordmark {
    position: absolute;
    left: 300px; top: 128px;
    width: 240px;
    text-align: center;
    color: var(--royal);
    font-size: 44px;
  }

  .contact {
    position: absolute;
    left: 36px; top: 150px;
    color: var(--white);
  }
  .contact__name {
    color: var(--gold);
    font-weight: 700;
    font-size: 19px;
    letter-spacing: 0.5px;
  }
  .contact__role { font-size: 14px; font-weight: 500; margin-top: 2px; }
  .contact__address { font-size: 13px; font-weight: 500; line-height: 1.4; margin-top: 14px; }
  .contact__list { list-style: none; margin-top: 10px; font-size: 13px; font-weight: 500; line-height: 1.55; }
  .contact__list li { display: flex; align-items: center; gap: 8px; }
  .contact__list svg { width: 11px; height: 11px; flex: none; }
</style>
</head>
<body>
  <section class="card card--front" aria-label="Business card front">
    <div class="wordmark">VKM Ltd</div>
  </section>

  <section class="card card--back" aria-label="Business card back">
    <svg class="back-art" viewBox="0 0 560 320" aria-hidden="true">
      <circle cx="408" cy="122" r="198" fill="var(--gold)"/>
      <circle cx="418" cy="116" r="196" fill="var(--white)"/>
    </svg>
    <div class="wordmark">VKM Ltd</div>

    <div class="contact">
      <p class="contact__name">DANIEL REYES</p>
      <p class="contact__role">Founder</p>
      <p class="contact__address">2815 Harbor Lane<br>Wilmington, DE 19801</p>
      <ul class="contact__list">
        <li>
          <svg viewBox="0 0 12 12"><path d="M2.5 1 L4.5 1 L5.2 3.5 L4 4.5 Q5 7 7.5 8 L8.5 6.8 L11 7.5 L11 9.5 Q10 11 8.5 11 Q2 9.5 1 3.5 Q1 2 2.5 1 Z" fill="var(--gold)"/></svg>
          (555) 210-7834
        </li>
        <li>
          <svg viewBox="0 0 12 12"><rect x="1" y="2.5" width="10" height="7" fill="none" stroke="var(--gold)" stroke-width="1.2"/><path d="M1 2.5 L6 6.5 L11 2.5" fill="none" stroke="var(--gold)" stroke-width="1.2"/></svg>
          info@VKMLtd.com
        </li>
        <li>
          <svg viewBox="0 0 12 12"><circle cx="6" cy="6" r="5" fill="none" stroke="var(--gold)" stroke-width="1.1"/><path d="M1 6 H11 M6 1 Q3 6 6 11 Q9 6 6 1" fill="none" stroke="var(--gold)" stroke-width="1"/></svg>
          www.VKMLtd.com
        </li>
      </ul>
    </div>
  </section>
</body>
</html>
```